Wordpress Site Design for a Horror and Action Movie Production Company

We need a re-design/facelift of our website: https://k42t.pagecraft.io
The structure of the website could remain the same, but it needs to look and feel BETTER!

We would like the website coded in Wordpress so that it can be easily updated bu us, via adding new projects and new projects' info.

We specialize in Action, Horror, and Sci-Fi Genre. That being said, we don't want the website to look like it's a themed park with haunted houses. It should still be sharp and professional, as after all - it is a business for us!

Target Market(s)

Film Distribution Companies (B2B), as well as general audience that likes movies

Industry/Entity Type

Movie Production

Coding

Coded - Design and coding required

Number of Pages Required

5+ page

Font styles to use
Sans Serif

Colors

Designer to choose colors to be used in the design.

Requirements
Must have
• - PROJECTS page
• - Each PROJECT has a sub-page with project info/updates (up dates could be in a form of a WP post, ideally a template that we can use to update and create new PROJECT pages, with text, poster, and video link (trailer))
• - NEWS page that chronologically lists updates from all PROJECTS (could be done via WP blog)
• - HOME page would
Nice to have
• Should generally have a dark background.
• Websites we like as a reference of general approach and style:
• https://marbletoq.com
• https://velunpix.com (however this is very image-centric, and we might not have that much imagery at the moment)
• https://www.copperfieldechoandframe.com/other
• https://quennreels.com
Should not have
• We specialize in Action, Horror, and Sci-Fi Genre. That being said, we don't want the website to look like it's a themed park with haunted houses. It should still be sharp and professional, as after all - it is a business for us!

```html
<!DOCTYPE html>
<html lang="en">
<head>
<meta charset="utf-8">
<title>Kestrel 42 Media</title>
<link href="https://fonts.googleapis.com/css2?family=Montserrat:wght@400;500;600;700&display=swap" rel="stylesheet">
<style>
:root{
  --black:#000;
  --ink:#0b0a0a;
  --panel:#100e0e;
  --white:#fff;
  --soft:#d9d9d9;
  --grey:#8a8a8a;
  --blood:#5a0a0c;
  --text-dark:#1a1a1a;
}
*{margin:0;padding:0;box-sizing:border-box}
html,body{width:1200px;height:3708px;overflow:hidden;background:var(--black)}
body{font-family:'Montserrat',sans-serif;color:var(--white);position:relative}
section,header,footer{position:absolute;left:0;width:1200px;overflow:hidden}
.abs{position:absolute}
.center{left:0;width:1200px;text-align:center}

.site-header{top:0;height:112px;background:var(--black)}
.brand{left:94px;top:38px;font-size:24px;font-weight:600;letter-spacing:1px;line-height:36px;padding-bottom:4px;border-bottom:1px solid var(--white)}
.nav{right:94px;top:44px;display:flex;gap:68px;font-size:20px;font-weight:500}
.nav a{color:var(--white);text-decoration:none}

.hero{top:112px;height:583px;background:radial-gradient(ellipse at 60% 35%,#5b5c4c 0%,#3a3a30 35%,#1c1a16 75%,#0d0c0b 100%)}
.hero-title{top:170px;font-size:62px;font-weight:700}
.hero-text{top:264px;left:140px;width:920px;text-align:center;font-size:19px;line-height:27px;font-weight:500}
.btn-ghost{border:2px solid var(--white);border-radius:40px;display:flex;align-items:center;justify-content:center;color:var(--white);font-weight:500}
.hero-btn{left:485px;top:347px;width:230px;height:61px;font-size:23px}
.dots{display:flex;gap:10px;justify-content:center}
.dot{width:14px;height:14px;border-radius:50%;border:2px solid var(--white)}
.dot.on{background:var(--white)}
.hero .dots{top:517px}

.about{top:695px;height:489px;background:radial-gradient(ellipse at 30% 50%,#3a0608 0%,#1d0405 50%,#0a0202 100%)}
.about h2{left:89px;top:78px;font-size:37px;font-weight:700}
.about p{left:89px;top:137px;width:496px;font-size:15.5px;line-height:33px;text-align:justify}
.about .btn-ghost{left:89px;top:370px;width:216px;height:56px;font-size:23px}
.about-photo{left:697px;top:71px;width:415px;height:356px;border:4px solid var(--white);background:linear-gradient(135deg,#6e5a44,#3d3a33 55%,#1e1d1b)}

.studios{top:1184px;height:425px;display:flex}
.studio{position:relative;width:600px;height:425px;background:var(--panel);text-align:center}
.studio + .studio{background:var(--black)}
.studio-mark{left:50%;transform:translateX(-50%);top:29px;height:75px;background:var(--white);color:var(--black);display:flex;align-items:center;gap:10px;padding:0 16px;font-size:17px;font-weight:700}
.studio-mark i{width:22px;height:22px;background:var(--black);display:block}
.studio h3{left:0;width:100%;top:140px;font-size:29px;font-weight:700}
.studio p{left:95px;width:480px;top:208px;font-size:15px;line-height:27px;text-align:justify;text-align-last:center}
.studio + .studio p{left:22px}

.projects{top:1609px;height:535px;background:linear-gradient(180deg,#151313,#0a0909)}
.projects h2{top:28px;font-size:40px;font-weight:700}
.projects .lead{top:88px;left:200px;width:800px;text-align:center;font-size:18px;line-height:27px;font-weight:500}
.tile{top:180px;height:279px}
.tile-1{left:89px;width:245px;background:linear-gradient(160deg,#2d2d2d,#121212)}
.tile-2{left:350px;width:243px;background:linear-gradient(100deg,#3a2d22,#8a7158 55%,#2b1f17)}
.tile-3{left:609px;width:244px;background:linear-gradient(150deg,#7a1a22,#3a0d12 50%,#b26a52)}
.tile-4{left:869px;width:243px;background:linear-gradient(140deg,#c9d0d8,#b59f94 55%,#6a7790)}
.projects .dots{top:495px}

.partners{top:2144px;height:587px;background:var(--ink)}
.partners h2{top:42px;font-size:40px;font-weight:700}
.card{top:186px;width:316px;height:290px;background:var(--white);color:var(--text-dark);text-align:center}
.card-1{left:91px}.card-2{left:442px}.card-3{left:793px}
.avatar{top:136px;width:136px;height:136px;border-radius:50%;border:5px solid var(--white);background:radial-gradient(circle at 50% 40%,#9a9a9a,#3a3a3a 70%);box-shadow:0 0 0 2px #bbb}
.av-1{left:181px}.av-2{left:532px}.av-3{left:883px}
.card h3{position:absolute;left:0;width:100%;top:98px;font-size:27px;font-weight:600}
.card p{position:absolute;left:20px;width:276px;top:150px;font-size:15.5px;line-height:27px}
.pill{width:137px;height:33px;border-radius:17px;background:#111;color:var(--white);font-size:15px;font-weight:500;display:flex;align-items:center;justify-content:center}
.partners .pill{top:465px}
.pl-1{left:180px}.pl-2{left:531px}.pl-3{left:882px}
.partners .dots{top:549px}

.contact{top:2731px;height:679px;background:linear-gradient(90deg,#c9c6c0 0%,#8f8c88 28%,#2c2a29 45%,#0d0c0c 60%,#0b0b0b 100%)}
.contact-photo{left:0;top:0;width:520px;height:679px;background:linear-gradient(90deg,rgba(210,205,198,.9),rgba(120,115,110,.5) 70%,rgba(20,20,20,0))}
.contact h2{left:515px;width:592px;text-align:center;top:54px;font-size:40px;font-weight:700}
.field{border:2px solid var(--white);color:var(--white);font-size:18px;padding:0 20px;display:flex;align-items:center}
.f-first{left:515px;top:141px;width:274px;height:64px}
.f-last{left:833px;top:141px;width:274px;height:64px}
.f-phone{left:515px;top:229px;width:274px;height:65px}
.f-email{left:833px;top:229px;width:274px;height:65px;padding-left:8px}
.f-msg{left:515px;top:320px;width:592px;height:208px;align-items:flex-start;padding-top:24px}
.contact .btn-ghost{left:695px;top:574px;width:232px;height:67px;font-size:23px}

.site-footer{top:3410px;height:298px;background:var(--black)}
.foot-brand{left:487px;width:226px;top:55px;text-align:center;font-size:32px;font-weight:600;letter-spacing:1px;padding-bottom:10px;border-bottom:2px solid var(--white)}
.foot-brand-sub{font-size:15px;letter-spacing:6px}
.foot-nav{top:182px;display:flex;justify-content:center;gap:36px;font-size:17px;font-weight:500}
.copyright{left:89px;top:253px;font-size:14px}
.social{right:94px;top:250px;display:flex;gap:14px;font-size:13px;font-weight:500}
</style>
</head>
<body>

<header class="site-header">
  <div class="abs brand">KESTREL 42 MEDIA</div>
  <nav class="abs nav"><a href="#">Home</a><a href="#">About</a><a href="#">News</a><a href="#">Projects</a><a href="#">Contact</a></nav>
</header>

<section class="hero" role="img" aria-label="Film still of a soldier in camouflage aiming a rifle in a smoky battlefield">
  <h1 class="abs center hero-title">Kestrel 42 Media</h1>
  <p class="abs hero-text">Kestrel 42 Media is a brain-child of a partnership between two Canadian companies, which for years have been recognizable brands in the Canadian media landscape:</p>
  <div class="abs btn-ghost hero-btn">GET A QUOTE</div>
  <div class="abs center dots"><span class="dot"></span><span class="dot on"></span><span class="dot"></span></div>
</section>

<section class="about">
  <h2 class="abs">About us Kestrel 42 Media</h2>
  <p class="abs">Kestrel 42 Media is a fresh brand of multi-media entertainment, aimed at the development of original Canadian content as well as servicing of foreign productions in Toronto, Ontario, Canada. We produce genre feature films, series, documentaries, and anything else that we feel great about.We take pride in our innovative approach.</p>
  <div class="abs btn-ghost">Read more</div>
  <div class="abs about-photo" role="img" aria-label="Behind-the-scenes photo of a film crew with lights on a living room set"></div>
</section>

<section class="studios">
  <div class="studio">
    <div class="abs studio-mark"><i></i>CORVID LANTERN</div>
    <h3 class="abs">Corvid Lantern Entertainment Inc</h3>
    <p class="abs">Corvid Lantern Entertainment is led by partners Marcus Delane, Adrian Holt and Jonas Brell. It represents unique, innovative and cutting edge genre films for North American distribution and the international marketplace. Through its expertise in strategic project management, Corvid Lantern Entertainment can assist in any and all stages of project production.</p>
  </div>
  <div class="studio">
    <div class="abs studio-mark"><i></i>NINE EMBER</div>
    <h3 class="abs">Nine Ember Entertainment Inc</h3>
    <p class="abs">Nine Ember Entertainment is founded by Pavel Rostan csc in 2015, and has since quickly gained momentum. It has been the name behind the production of a feature film Pushed Past Dawn, a festival darling feature Hollow Verge, a number of short films, web series pilots, and is currently in development of a number of original properties.</p>
  </div>
</section>

<section class="projects">
  <h2 class="abs center">PROJECTS</h2>
  <p class="abs lead">Below is a list of links to some of the recent projects, produced and/or production serviced by Corvid Lantern or Nine Ember Entertainment:</p>
  <div class="abs tile tile-1" role="img" aria-label="Dark movie poster with a title over a shadowed face"></div>
  <div class="abs tile tile-2" role="img" aria-label="Movie poster of a boxer standing by a window"></div>
  <div class="abs tile tile-3" role="img" aria-label="Red movie poster with a shattered fan and a figure below"></div>
  <div class="abs tile tile-4" role="img" aria-label="Movie poster of tattooed hands covering a face"></div>
  <div class="abs center dots"><span class="dot"></span><span class="dot on"></span><span class="dot"></span></div>
</section>

<section class="partners">
  <h2 class="abs center">PARTNERS</h2>
  <div class="abs card card-1"><h3>Adrian Holt</h3><p>Adrian T Holt is an award-winning Writer/Producer/Director with over 15 years experience in the film and television industry.</p></div>
  <div class="abs card card-2"><h3>Pavel Rostan</h3><p>Pavel Rostan is a 18-year-long veteran of the film biz. Starting out as a cinematographer, he developed a unique visual style</p></div>
  <div class="abs card card-3"><h3>Jonas Brell</h3><p>Jonas Brell has taken a decidedly different path to the film industry than his partners have. A successful entrepreneur for over 20 years</p></div>
  <div class="abs avatar av-1" role="img" aria-label="Portrait photo of Adrian Holt"></div>
  <div class="abs avatar av-2" role="img" aria-label="Portrait photo of Pavel Rostan"></div>
  <div class="abs avatar av-3" role="img" aria-label="Portrait photo of Jonas Brell"></div>
  <div class="abs pill pl-1">Read More</div>
  <div class="abs pill pl-2">Read More</div>
  <div class="abs pill pl-3">Read More</div>
  <div class="abs center dots"><span class="dot"></span><span class="dot on"></span><span class="dot"></span></div>
</section>

<section class="contact">
  <div class="abs contact-photo" role="img" aria-label="Photo of a man in a white shirt filming with a vintage camera"></div>
  <h2 class="abs">CONTACT US</h2>
  <div class="abs field f-first">First name</div>
  <div class="abs field f-last">Last name</div>
  <div class="abs field f-phone">Phone number</div>
  <div class="abs field f-email">Email</div>
  <div class="abs field f-msg">Messages</div>
  <div class="abs btn-ghost">Submit</div>
</section>

<footer class="site-footer">
  <div class="abs foot-brand">KESTREL 42<br><span class="foot-brand-sub">MEDIA</span></div>
  <nav class="abs center foot-nav"><span>Home</span><span>About</span><span>News</span><span>Projects</span><span>Contact</span></nav>
  <div class="abs copyright">© 2019 KESTREL 42 MEDIA | All Rights Reserved.</div>
  <div class="abs social"><span>Flick</span><span>Snapo</span><span>Linkly</span><span>Vidra</span></div>
</footer>

</body>
</html>
```